OpenHarbor Yoga Website Design

Business Logo - attached
5 pages being:
Home
About
Classes
Blog
Contact

Would like Scrolling webpage and yoga symbols to be used.

Must have's being:
Easy to navigate, Text needs to be able to be edited/updated, Enquire Now Links, More Information Links, be a secure site, SEO,

Please refer to attached document for the information for the body of the website.

Target Market(s)

Educators, Community Service, Health and Wellbeing, Mental Health

Industry/Entity Type

Yoga

Coding

Coded - Design and coding required

Number of Pages Required

5+ page

Font styles to use
Other font styles liked:
• Bella Bold BC

Colors
0094D4
00A9DD
6FCCEA
C7EBF8
E9F6FB
6B429C
8869AF
B7A5CE
E3DAEB
F3F0F8

Requirements
Must have
• Easy to navigate, Text needs to be able to be edited/updated, Enquire Now Links, More Information Links, be a secure site, SEO,
Nice to have
• Scrolling webpage, yoga symbols

```html
<!DOCTYPE html>
<html lang="en">
<head>
<meta charset="utf-8">
<title>OpenHarbor Yoga</title>
<link href="https://fonts.googleapis.com/css2?family=Montserrat:wght@400;500;600;700&family=Lato:wght@400;700&family=Kaushan+Script&display=swap" rel="stylesheet">
<style>
:root{
  --violet:#5a14c8;
  --violet-mid:#8a4fe0;
  --lilac:#c9a8f2;
  --lilac-soft:#e3d6f6;
  --ink:#111111;
  --text:#2b2b2b;
  --muted:#555555;
  --hero-bg:#ececec;
  --band-bg:#f5f5f5;
  --white:#ffffff;
  --rule:#d9d9d9;
}
*{margin:0;padding:0;box-sizing:border-box}
html,body{width:1200px;height:2943px;overflow:hidden}
body{position:relative;background:var(--white);font-family:'Lato',sans-serif;color:var(--text)}
.abs{position:absolute}
.eyebrow{font-family:'Montserrat',sans-serif;font-weight:700;color:var(--violet);font-size:22px;letter-spacing:.2px}
.script{font-family:'Kaushan Script',cursive;color:var(--ink);line-height:1;white-space:nowrap}
.copy{font-size:15.5px;line-height:26px;color:var(--text)}
.pill{display:inline-flex;align-items:center;gap:14px;height:48px;padding:0 22px 0 5px;border-radius:24px;background:var(--violet);color:var(--white);font-family:'Montserrat',sans-serif;font-weight:700;font-size:13px;text-transform:uppercase;white-space:nowrap}
.pill .dot{width:38px;height:38px;border-radius:50%;background:var(--lilac-soft);flex:none}

/* hero */
.hero{left:0;top:0;width:1200px;height:714px;background:var(--hero-bg);overflow:hidden}
.call{left:112px;top:42px;display:flex;align-items:center;gap:10px;font-family:'Montserrat',sans-serif}
.call .icon{width:38px;height:38px;border-radius:50%;background:var(--violet);display:flex;align-items:center;justify-content:center}
.call small{display:block;color:var(--violet);font-weight:600;font-size:15px}
.call strong{display:block;font-size:19px;font-weight:700;color:var(--ink)}
.brand{left:500px;top:55px;width:200px;text-align:center;display:flex;align-items:center;justify-content:center;gap:8px;font-family:'Lato',sans-serif;font-weight:700;font-size:17px;color:var(--violet)}
.brand i{width:14px;height:14px;border-radius:50%;background:var(--violet);display:block}
.nav{left:734px;top:52px;display:flex;gap:34px;font-family:'Montserrat',sans-serif;font-size:15px;color:#333}
.nav .active{color:var(--violet)}
.hero-title{left:110px;top:240px;font-size:60px}
.hero-copy{left:112px;top:344px;width:480px;font-size:14px;line-height:26px}
.hero-btn{left:111px;top:469px}
.hero-art{left:640px;top:110px;width:500px;height:590px;border-radius:250px 250px 30px 30px;background:radial-gradient(ellipse at 50% 45%,#ffffff 0%,#e6dcf6 45%,#b993ee 80%,#7a3ee0 100%)}

/* about */
.about-art{left:118px;top:870px;width:420px;height:420px;border-radius:50%;background:radial-gradient(circle at 45% 40%,#f4f1f6 0%,#dcd6e2 60%,#b9a5d8 100%);box-shadow:-40px 20px 0 20px rgba(157,110,230,.35)}
.about-badge{left:455px;top:1178px;width:88px;height:88px;border-radius:50%;background:var(--white);box-shadow:0 6px 18px rgba(0,0,0,.12);display:flex;align-items:center;justify-content:center}
.about-text{left:641px;top:858px;width:460px}
.about-text .script{font-size:54px;margin:14px 0 18px}
.about-text p{font-size:15.5px;line-height:26px;margin-bottom:26px}

/* benefits */
.benefits{left:0;top:1452px;width:1200px;height:793px;background:var(--band-bg)}
.benefits-head{left:110px;top:82px;width:560px}
.benefits-head .script{font-size:54px;margin:8px 0 14px}
.card{top:286px;width:315px;height:420px}
.card .photo{width:315px;height:328px}
.card .panel{position:absolute;left:9px;top:283px;width:297px;background:var(--white);padding:12px 16px 16px}
.card h3{font-family:'Kaushan Script',cursive;font-weight:400;font-size:25px;color:var(--ink);margin-bottom:6px}
.card li{list-style:none;font-size:13px;line-height:23px;color:var(--text)}
.card .go{position:absolute;right:0;bottom:-18px;width:36px;height:36px;background:var(--violet);display:flex;align-items:center;justify-content:center}

/* newsletter */
.newsletter{left:0;top:2345px;width:1200px;text-align:center}
.newsletter .script{font-size:48px;margin:12px 0 14px}
.newsletter p{font-size:15.5px;color:var(--muted)}
.subscribe{left:278px;top:2500px;width:643px;height:55px;border-radius:28px;background:var(--white);box-shadow:0 4px 20px rgba(0,0,0,.06);display:flex;align-items:center}
.subscribe span{margin-left:26px;display:flex;align-items:center;gap:14px;color:#888;font-size:14.5px;flex:1}
.subscribe b{width:140px;height:53px;border-radius:27px;background:var(--violet);color:var(--white);font-family:'Montserrat',sans-serif;font-weight:700;font-size:16px;display:flex;align-items:center;justify-content:center}

/* footer */
.foot-brand{left:150px;top:2690px;width:210px;display:flex;align-items:center;gap:10px;font-family:'Lato',sans-serif;font-weight:700;font-size:22px;color:var(--violet)}
.foot-brand i{width:22px;height:22px;border-radius:50%;background:var(--violet);display:block;flex:none}
.foot-col h4{font-family:'Montserrat',sans-serif;font-weight:700;font-size:18px;color:var(--ink);margin-bottom:18px}
.foot-col li{list-style:none;font-size:15.5px;line-height:30px;color:var(--text)}
.contact li{display:flex;gap:12px;line-height:24px;margin-bottom:12px}
.contact svg{flex:none;margin-top:5px}
.social{display:flex;gap:8px;margin-bottom:26px}
.social span{width:32px;height:32px;border-radius:50%;display:block}
.abn{font-family:'Montserrat',sans-serif;font-weight:600;font-size:15px;color:var(--ink)}
.rule{left:112px;top:2855px;width:976px;height:1px;background:var(--rule)}
.copyright{left:0;top:2886px;width:1200px;text-align:center;font-size:15px;color:var(--text)}
</style>
</head>
<body>

<section class="abs hero">
  <div class="abs call">
    <span class="icon"><svg width="16" height="16" viewBox="0 0 24 24"><path fill="#fff" d="M6.6 10.8a15 15 0 0 0 6.6 6.6l2.2-2.2c.3-.3.7-.4 1-.2 1.1.4 2.3.6 3.6.6.6 0 1 .4 1 1V20c0 .6-.4 1-1 1A17 17 0 0 1 3 4c0-.6.4-1 1-1h3.5c.6 0 1 .4 1 1 0 1.3.2 2.5.6 3.6.1.3 0 .7-.2 1z"/></svg></span>
    <div><small>Call Us</small><strong>0400 123 456</strong></div>
  </div>
  <div class="abs brand"><i></i>OpenHarbor Yoga</div>
  <nav class="abs nav"><span class="active">Home</span><span>About Us</span><span>Our Blog</span><span>Contact Us</span></nav>

  <div class="abs hero-art" role="img" aria-label="Woman in white activewear holding a warrior yoga pose on a mat, framed by purple flowing shapes and dots"></div>
  <div class="abs eyebrow" style="left:112px;top:198px">WELCOME TO</div>
  <h1 class="abs script hero-title">OpenHarbor Yoga</h1>
  <p class="abs hero-copy">OpenHarbor Yoga believe that you are never too young to benefit from and fall in love with yoga.&nbsp; My aim is to EMPOWER kids and teens to thrive by teaching life skills in Yoga, Mindfulness and Breathing techniques to deal with daily challenges and big emotions.</p>
  <div class="abs pill hero-btn"><span class="dot"></span>Get Started</div>
</section>

<div class="abs about-art" role="img" aria-label="Woman in pastel activewear stretching on a mat in a bright room, inside a circle with purple paint splashes"></div>
<div class="abs about-badge"><svg width="40" height="40" viewBox="0 0 40 40" fill="none" stroke="#5a14c8" stroke-width="2"><circle cx="27" cy="8" r="3"/><path d="M26 12 18 22l-8 8M18 22l10 8M4 34h32"/></svg></div>
<div class="abs about-text">
  <div class="eyebrow">ABOUT US</div>
  <h2 class="script">OpenHarbor Yoga</h2>
  <p>Hi and welcome to OpenHarbor Yoga!<br>My name is Renata, and I am the creator &amp; facilitator of OpenHarbor Yoga.</p>
  <p>With the increasing numbers of youth mental health, I have started OpenHarbor Yoga wanting to assist children and teens with their mental health for life, with the magic of yoga.</p>
  <p>I had always wanted to teach children, but had never found the right platform to do so... That was until I found yoga!</p>
  <div class="pill"><span class="dot"></span>Leran More</div>
</div>

<section class="abs benefits">
  <div class="abs benefits-head">
    <div class="eyebrow">BENEFITS</div>
    <h2 class="script">Benefits of Yoga...</h2>
    <p class="copy">The benefits of yoga can last a lifetime. It is my aim &amp; passion to introduce yoga to kids of all ages and backgrounds so that they can not only experience the benefits of yoga but fall in love with the practice.</p>
  </div>

  <article class="abs card" style="left:111px">
    <div class="photo" role="img" aria-label="Woman doing a side stretch on a mat in a light living room" style="background:linear-gradient(160deg,#e9e9ea,#c9cdd0 60%,#5f8a90)"></div>
    <div class="panel">
      <h3>Healthy bodies</h3>
      <ul><li>• Develops strong, flexible and healthy bodies</li><li>• Promotes spinal alignment and good posture</li></ul>
      <span class="go"><svg width="16" height="16" viewBox="0 0 16 16" fill="none" stroke="#fff" stroke-width="2"><path d="M2 8h11M9 4l4 4-4 4"/></svg></span>
    </div>
  </article>

  <article class="abs card" style="left:481px">
    <div class="photo" role="img" aria-label="Woman meditating cross-legged in a calm room" style="background:linear-gradient(160deg,#f1e9e2,#d9c6b6 60%,#8c6d5c)"></div>
    <div class="panel">
      <h3>Healthy minds</h3>
      <ul><li>•Cultivates confidence and self-esteem</li><li>•Develops concentration and attention</li></ul>
      <span class="go"><svg width="16" height="16" viewBox="0 0 16 16" fill="none" stroke="#fff" stroke-width="2"><path d="M2 8h11M9 4l4 4-4 4"/></svg></span>
    </div>
  </article>

  <article class="abs card" style="left:850px">
    <div class="photo" role="img" aria-label="Person sitting on rocks before a forest waterfall" style="background:linear-gradient(170deg,#3f4a3a,#6b7a70 45%,#2a2a26)"></div>
    <div class="panel">
      <h3>Healthy spirits</h3>
      <ul><li>• Fosters creativity, expression and imagination</li><li>• Cultivates kindness to themselves and<br>&nbsp;&nbsp;others</li></ul>
      <span class="go"><svg width="16" height="16" viewBox="0 0 16 16" fill="none" stroke="#fff" stroke-width="2"><path d="M2 8h11M9 4l4 4-4 4"/></svg></span>
    </div>
  </article>
</section>

<section class="abs newsletter">
  <div class="eyebrow">OUR NEWSLETTER</div>
  <h2 class="script">Subscribe to our newsletter</h2>
  <p>Lorem ipsum dolor sit amet, consectetur adipiscing elit</p>
</section>
<div class="abs subscribe">
  <span><svg width="16" height="16" viewBox="0 0 24 24"><path fill="#5a14c8" d="M22 2 2 10l7 3 3 9z"/></svg>Enter Your Email</span>
  <b>SUBSCRIBE</b>
</div>

<div class="abs foot-brand"><i></i>OpenHarbor Yoga</div>

<div class="abs foot-col contact" style="left:448px;top:2636px;width:240px">
  <h4>CONTACT US</h4>
  <ul>
    <li><svg width="12" height="14" viewBox="0 0 12 16"><path fill="#5a14c8" d="M6 0a6 6 0 0 0-6 6c0 4.5 6 10 6 10s6-5.5 6-10a6 6 0 0 0-6-6zm0 8.5A2.5 2.5 0 1 1 6 3.5a2.5 2.5 0 0 1 0 5z"/></svg>Fernvale, Victoria Australia 3999</li>
    <li><svg width="13" height="13" viewBox="0 0 24 24"><path fill="#5a14c8" d="M6.6 10.8a15 15 0 0 0 6.6 6.6l2.2-2.2c.3-.3.7-.4 1-.2 1.1.4 2.3.6 3.6.6.6 0 1 .4 1 1V20c0 .6-.4 1-1 1A17 17 0 0 1 3 4c0-.6.4-1 1-1h3.5c.6 0 1 .4 1 1 0 1.3.2 2.5.6 3.6.1.3 0 .7-.2 1z"/></svg>0400 123 456</li>
    <li><svg width="15" height="12" viewBox="0 0 20 16"><path fill="#5a14c8" d="M0 0h20v16H0zm2 2v1l8 5 8-5V2z"/></svg>hello@openharboryoga.example</li>
  </ul>
</div>

<div class="abs foot-col" style="left:727px;top:2636px">
  <h4>SUPPORT</h4>
  <ul><li>Terms &amp; Conditions</li><li>Contact Us</li><li>Privacy Policy</li><li>Enquire Now</li><li>More Information</li></ul>
</div>

<div class="abs foot-col" style="left:925px;top:2636px">
  <h4>FOLLOW US</h4>
  <div class="social" aria-label="Social links">
    <span style="background:var(--violet)"></span>
    <span style="background:var(--lilac-soft)"></span>
  </div>
  <div class="abn">ABN:&nbsp; 12 345 678 901</div>
</div>

<div class="abs rule"></div>
<div class="abs copyright">©Copyrights 2023 OpenHarbor Yoga &nbsp;&nbsp;|&nbsp;&nbsp;&nbsp; All Rights Reserved</div>

</body>
</html>
```